CREATE A KILLER WEBSITE DESIGN

We are a firearms training company that trains CIVILIANS (no police or military pictures - thank you!) to defend themselves and are looking for a killer design that's clean, easy to navigate and modern! We want the newest trends applied to this sight like a scrollable site so you can scroll down and see all the features. We are okay with tweaking the HTML but need the artistic design to look good. I'll provide a link to our current site along with a sight we really like so you can get an idea!

I'm supplying a PowerPoint Design we are going with from another designer so you can match the style to the new site.

PAGES: (Please use information from our current site. We like the information but just want a more polished look similar to the NWDPA site below but in our colors.)
Home - Long Form Scrolling Site. Top fold will be a video with a play button.
Harbor Institute - Seven Level Training Program Info Page That Will Contain A Video.
Contact Us - This will be a page that DOES NOT CONTAIN AN EMAIL ADDRESS. Just a contact us form
Meet The Trainer: Dennis Pollock

Our site:
https://www.brightmeadowskills.biz

Sights We Like:
https://www.nwdefenseplanners.com
https://quorvel.com
https://lindenplatecorp.com
https://www.velbrookgear.com

Target Market(s)

Men and women ages 21 to 100 years old

Industry/Entity Type

Self Defense

Number of Pages Required

5+ page

Font styles to use
Sans Serif

Colors
f26267

Requirements
Must have
• Clean and engaging. Use of colors that match our logo.
Should not have
• Poor design quality

```html
<!DOCTYPE html>
<html lang="en">
<head>
<meta charset="utf-8">
<title>Level 5 – Tactical Skills &amp; Drills | Steadfield Carry Training</title>
<link href="https://fonts.googleapis.com/css2?family=Barlow:wght@300;400;500&family=Rajdhani:wght@600;700&family=Michroma&display=swap" rel="stylesheet">
<style>
:root{
  --red:#d71f26;
  --ink:#222326;
  --dark:#1e1f21;
  --darker:#161718;
  --text:#6d6e71;
  --muted:#9a9b9e;
  --white:#ffffff;
  --line:#3a3b3e;
}
*{box-sizing:border-box;margin:0;padding:0}
html,body{width:1200px;height:2680px;overflow:hidden}
body{position:relative;background:var(--white);font-family:"Barlow",sans-serif;font-weight:300;color:var(--text)}
.abs{position:absolute}
a{color:inherit;text-decoration:none}

/* hero */
.hero{left:0;top:0;width:1200px;height:370px;background:linear-gradient(100deg,#4a4440 0%,#6b625b 35%,#57514d 60%,#3a3634 100%);border-bottom:4px solid var(--red)}
.hero-shade{left:0;top:0;width:1200px;height:366px;background:rgba(20,20,22,.45)}
.brand{left:60px;top:28px;display:flex;align-items:center;gap:14px}
.brand-mark{width:62px;height:62px;border-radius:50%;border:4px solid var(--red)}
.brand-name{font-family:"Rajdhani",sans-serif;font-weight:700;font-size:30px;color:var(--white);line-height:1;letter-spacing:1px}
.notice{left:535px;top:13px;width:560px;font-size:12.5px;color:#e6e6e6;line-height:16px;font-weight:400}
.notice b{font-weight:500}
.notice-arrows{left:1118px;top:14px}
.account{left:740px;top:55px;width:185px;height:46px;background:var(--darker);clip-path:polygon(14px 0,100% 0,100% 100%,0 100%);display:flex;align-items:center;gap:10px;padding-left:34px;color:var(--white);font-size:11px;line-height:13px;font-weight:400}
.account svg{flex:none}
.urgent{left:921px;top:55px;width:214px;height:42px;background:var(--red);clip-path:polygon(12px 0,100% 0,100% 100%,0 100%);color:var(--white);font-family:"Rajdhani",sans-serif;font-weight:700;font-size:14px;display:flex;align-items:center;justify-content:center}
.nav{left:60px;top:103px;width:1080px;height:54px;background:var(--ink);display:flex;align-items:center;justify-content:space-around;padding:0 22px}
.nav a{font-family:"Rajdhani",sans-serif;font-weight:700;font-size:15.5px;color:var(--white);letter-spacing:.3px}
.hero-level{left:0;width:1200px;top:200px;text-align:center;font-family:"Rajdhani",sans-serif;font-weight:700;font-size:21px;color:var(--red)}
.hero-level sup{font-size:11px}
.hero-title{left:0;width:1200px;top:236px;text-align:center;font-family:"Michroma",sans-serif;font-size:29px;color:var(--white);letter-spacing:.5px}
.crumbs{left:0;width:1200px;top:280px;text-align:center;font-size:14px;color:#eee;font-weight:400}

/* intro */
.intro{left:125px;width:950px;top:438px;text-align:center;font-size:16.5px;line-height:26.5px}
.intro .warn{color:var(--red);font-weight:500;font-size:16px}
.btn{height:40px;display:flex;align-items:center;justify-content:center;color:var(--white);font-size:14.5px;font-weight:400;clip-path:polygon(6px 0,100% 0,calc(100% - 6px) 100%,0 100%)}
.btn-red{background:var(--red)}
.btn-dark{background:var(--ink)}

/* video */
.band{left:0;top:835px;width:1200px;height:213px;background:var(--red)}
.video{left:224px;top:678px;width:750px;height:422px;background:linear-gradient(160deg,#c9d2d8 0%,#aebdb2 30%,#4f6a35 52%,#6a5a4a 75%,#3a3330 100%)}
.play{left:559px;top:842px}

/* lists */
.h2{font-family:"Rajdhani",sans-serif;font-weight:700;font-size:27px;color:var(--ink);letter-spacing:1px}
.list{list-style:none;font-size:16px;line-height:26.5px}
.list li{display:flex;align-items:center;gap:12px}
.list li svg{flex:none}
.list li.note{display:block;padding-left:29px;font-family:"Rajdhani",sans-serif;font-weight:600;font-size:16px;color:#55565a}
.list .note em{font-style:normal;color:var(--red)}
.rental{left:140px;width:920px;top:1530px;text-align:center;line-height:33px}
.rental span{color:var(--red)}
.rental-note{left:119px;top:1614px;font-size:16px}

/* info */
.divider{left:595px;top:1856px;width:2px;height:140px;background:var(--red)}
.contact-line{font-size:16px;line-height:26.5px}
.contact-line a{color:var(--red);font-weight:500;font-style:italic}

/* footer */
.footer{left:0;top:2103px;width:1200px;height:577px;background:var(--dark)}
.footer-base{left:0;top:2533px;width:1200px;height:147px;background:var(--darker)}
.footer-mark{left:570px;top:2072px;width:60px;height:60px;border-radius:50%;background:var(--dark);border:5px solid var(--red)}
.news-title{left:60px;top:2155px;font-family:"Rajdhani",sans-serif;font-weight:700;font-size:22px;color:var(--white);letter-spacing:.5px}
.news-sub{left:60px;top:2189px;font-size:14.5px;color:#e0e0e0;font-weight:400}
.news-input{left:671px;top:2158px;width:330px;height:50px;background:#2c2d30;color:#8d8e91;font-size:16px;display:flex;align-items:center;padding-left:42px;letter-spacing:.8px;font-weight:400}
.news-btn{left:992px;top:2158px;width:148px;height:50px;background:var(--red);clip-path:polygon(10px 0,100% 0,100% 100%,0 100%);color:var(--white);font-family:"Rajdhani",sans-serif;font-weight:700;font-size:16px;display:flex;align-items:center;justify-content:center}
.rule{left:34px;top:2250px;width:1134px;height:1px;background:var(--line)}
.col-title{top:2298px;font-family:"Rajdhani",sans-serif;font-weight:700;font-size:16px;color:var(--red);letter-spacing:.3px}
.col{top:2329px;list-style:none;font-size:14.5px;line-height:26.5px;color:#e4e4e4;font-weight:400}
.social{left:967px;top:2330px;display:flex;gap:12px}
.social span{width:20px;height:20px;background:var(--white);border-radius:2px}
.card{left:60px;top:2497px;width:1080px;height:135px;background:#f4f4f4}
.trainer{left:141px;top:2514px;font-family:"Rajdhani",sans-serif;font-weight:700;font-size:23px;color:var(--ink);letter-spacing:1px}
.trainer-role{left:141px;top:2550px;width:320px;font-size:13.5px;line-height:16.5px;color:#8a8b8e;font-weight:400}
.card-info{font-size:13.5px;line-height:17px;color:#8a8b8e;font-weight:400}
.copy{left:0;width:1200px;top:2648px;text-align:center;font-size:13.5px;color:#e4e4e4;font-weight:400}
</style>
</head>
<body>

<!-- Hero -->
<div class="abs hero" role="img" aria-label="Photo of a student firing a handgun at an outdoor range"></div>
<div class="abs hero-shade"></div>

<div class="abs brand">
  <span class="brand-mark"></span>
  <span class="brand-name">STEADFIELD<br>CARRY TRAINING</span>
</div>

<p class="abs notice"><b>Steadfield Carry Training &amp; Harbor Institute Response :</b> Masks Required, All Student's Temperature Checked &amp; Facilities Sanatized For Your Safety!</p>
<svg class="abs notice-arrows" width="14" height="26" viewBox="0 0 14 26"><path d="M2 8 7 3l5 5M2 18l5 5 5-5" fill="none" stroke="#fff" stroke-width="1.4"/></svg>

<div class="abs account">
  <svg width="24" height="24" viewBox="0 0 24 24"><circle cx="12" cy="12" r="11" fill="none" stroke="#fff" stroke-width="1.2"/><circle cx="12" cy="9.5" r="3" fill="none" stroke="#fff" stroke-width="1.2"/><path d="M7 17c1-2.5 3-3.5 5-3.5s4 1 5 3.5" fill="none" stroke="#fff" stroke-width="1.2"/></svg>
  <span><b style="font-weight:500">Sign In or</b><br>Create An Account</span>
</div>
<a class="abs urgent" href="#">I NEED IMMEDIATE SERVICE</a>

<nav class="abs nav">
  <a href="#">HOME</a><a href="#">HARBOR INSTITUTE</a><a href="#">TESTIMONIALS</a><a href="#">ABOUT</a><a href="#">UPCOMING CLASSES</a><a href="#">SHOP</a><a href="#">VIDEOS</a><a href="#">LOST CERTIFICATE</a><a href="#">CONTACT US</a>
</nav>

<p class="abs hero-level">5<sup>TH</sup> LEVEL</p>
<h1 class="abs hero-title">TACTICAL SKILLS &amp; DRILLS</h1>
<p class="abs crumbs">home / harbor-institute / level-5</p>

<!-- Intro -->
<p class="abs intro">This is the 5th level in our training system! We will build upon the previous training levels and teach you how to fight with a handgun in combat situations using live fire in an outdoor tactical training environment! This is where we apply our defensive shooting in the context of real-life situations.<br><span class="warn">**STUDENTS MUST HAVE COMPLETED LEVELS 1 through 4 IN ORDER TO ATTEND THIS TRAINING**</span></p>

<a class="abs btn btn-red" href="#" style="left:352px;top:572px;width:173px">ENROLL TODAY</a>
<a class="abs btn btn-dark" href="#" style="left:529px;top:572px;width:315px">GET ADVANCED HANDS ON TRAINING</a>

<!-- Video -->
<div class="abs band"></div>
<div class="abs video" role="img" aria-label="Training video still of a woman aiming a handgun at an outdoor range"></div>
<svg class="abs play" width="82" height="82" viewBox="0 0 82 82"><circle cx="41" cy="41" r="22" fill="#fff"/><path d="M35 30 54 41 35 52Z" fill="#222326"/></svg>

<!-- Requirements -->
<h2 class="abs h2" style="left:121px;top:1180px">REQUIREMENTS:</h2>
<ul class="abs list" style="left:121px;top:1225px">
  <li><svg width="17" height="17" viewBox="0 0 17 17"><circle cx="8.5" cy="8.5" r="7.5" fill="none" stroke="#d71f26" stroke-width="1.5"/><circle cx="8.5" cy="8.5" r="4.3" fill="none" stroke="#d71f26" stroke-width="1.5"/><circle cx="8.5" cy="8.5" r="1.6" fill="#d71f26"/></svg>Defensive Handgun &amp; EXTERNAL HIP HOLSTER</li>
  <li><svg width="17" height="17" viewBox="0 0 17 17"><circle cx="8.5" cy="8.5" r="7.5" fill="none" stroke="#d71f26" stroke-width="1.5"/><circle cx="8.5" cy="8.5" r="4.3" fill="none" stroke="#d71f26" stroke-width="1.5"/><circle cx="8.5" cy="8.5" r="1.6" fill="#d71f26"/></svg>A Minimum of 250 Rounds of Ammo</li>
  <li class="note">[WE HAVE LIMITED AMMO FOR SALE BUT YOU MUST TEXT <em>555-014-5822</em> IN ADVANCE TO ARRANGE IT]</li>
  <li><svg width="17" height="17" viewBox="0 0 17 17"><circle cx="8.5" cy="8.5" r="7.5" fill="none" stroke="#d71f26" stroke-width="1.5"/><circle cx="8.5" cy="8.5" r="4.3" fill="none" stroke="#d71f26" stroke-width="1.5"/><circle cx="8.5" cy="8.5" r="1.6" fill="#d71f26"/></svg>Water, Snacks &amp; Lunch</li>
</ul>

<h2 class="abs h2" style="left:121px;top:1391px">OPTIONAL:</h2>
<ul class="abs list" style="left:121px;top:1436px">
  <li><svg width="17" height="17" viewBox="0 0 17 17"><circle cx="8.5" cy="8.5" r="7.5" fill="none" stroke="#d71f26" stroke-width="1.5"/><circle cx="8.5" cy="8.5" r="4.3" fill="none" stroke="#d71f26" stroke-width="1.5"/><circle cx="8.5" cy="8.5" r="1.6" fill="#d71f26"/></svg>Inside The Waistband Holster</li>
</ul>

<!-- Rentals -->
<h2 class="abs h2 rental">RENTAL GUNS AVAILABLE FOR <span>$39.95</span> PER DAY INCLUDING MATCHING HOLSTER &amp; MAGAZINES</h2>
<p class="abs rental-note">(limited availability on a first-come / first-served basis and paid by CC in advance. Please call ahead to reserve a rental gun)</p>
<ul class="abs list" style="left:121px;top:1664px">
  <li><svg width="17" height="17" viewBox="0 0 17 17"><circle cx="8.5" cy="8.5" r="7.5" fill="none" stroke="#d71f26" stroke-width="1.5"/><circle cx="8.5" cy="8.5" r="4.3" fill="none" stroke="#d71f26" stroke-width="1.5"/><circle cx="8.5" cy="8.5" r="1.6" fill="#d71f26"/></svg>Kestrel Compact K4 &amp; Matching Holster</li>
  <li><svg width="17" height="17" viewBox="0 0 17 17"><circle cx="8.5" cy="8.5" r="7.5" fill="none" stroke="#d71f26" stroke-width="1.5"/><circle cx="8.5" cy="8.5" r="4.3" fill="none" stroke="#d71f26" stroke-width="1.5"/><circle cx="8.5" cy="8.5" r="1.6" fill="#d71f26"/></svg>Arlen Carry One &amp; Matching Holster</li>
  <li><svg width="17" height="17" viewBox="0 0 17 17"><circle cx="8.5" cy="8.5" r="7.5" fill="none" stroke="#d71f26" stroke-width="1.5"/><circle cx="8.5" cy="8.5" r="4.3" fill="none" stroke="#d71f26" stroke-width="1.5"/><circle cx="8.5" cy="8.5" r="1.6" fill="#d71f26"/></svg>Halden &amp; Roe Guard &amp; Holster</li>
  <li><svg width="17" height="17" viewBox="0 0 17 17"><circle cx="8.5" cy="8.5" r="7.5" fill="none" stroke="#d71f26" stroke-width="1.5"/><circle cx="8.5" cy="8.5" r="4.3" fill="none" stroke="#d71f26" stroke-width="1.5"/><circle cx="8.5" cy="8.5" r="1.6" fill="#d71f26"/></svg>Halden &amp; Roe Easy Guard &amp; Holster</li>
  <li><svg width="17" height="17" viewBox="0 0 17 17"><circle cx="8.5" cy="8.5" r="7.5" fill="none" stroke="#d71f26" stroke-width="1.5"/><circle cx="8.5" cy="8.5" r="4.3" fill="none" stroke="#d71f26" stroke-width="1.5"/><circle cx="8.5" cy="8.5" r="1.6" fill="#d71f26"/></svg>Halden &amp; Roe Service Mk II &amp; Holster</li>
</ul>

<!-- Questions / Booking -->
<h2 class="abs h2" style="left:121px;top:1865px">HAVE QUESTIONS?</h2>
<p class="abs contact-line" style="left:119px;top:1911px">CALL US : <a href="#">+800-555-0172</a><br>EMAIL US : <a href="#">steadfieldcarry@example.com</a></p>
<div class="abs divider"></div>
<h2 class="abs h2" style="left:720px;top:1865px">BOOKING POLICY</h2>
<p class="abs contact-line" style="left:720px;top:1911px">Bookings close 1 day before the session starts.</p>
<a class="abs btn btn-red" href="#" style="left:723px;top:1953px;width:173px">ENROLL TODAY</a>

<!-- Footer -->
<footer>
  <div class="abs footer"></div>
  <div class="abs footer-base"></div>
  <div class="abs footer-mark"></div>

  <h3 class="abs news-title">SUBSCRIBE TO OUR NEWSLETTER!</h3>
  <p class="abs news-sub">Be the first to grab our exclusive offers, promotions and news. Subscribe Today!</p>
  <div class="abs news-input">Enter your email</div>
  <a class="abs news-btn" href="#">SUBSCRIBE</a>
  <div class="abs rule"></div>

  <h4 class="abs col-title" style="left:60px">QUICK LINKS</h4>
  <ul class="abs col" style="left:60px"><li>Harbor Institute</li><li>Testimonials</li><li>About</li><li>Upcoming Classes</li><li>Shop</li></ul>
  <ul class="abs col" style="left:271px"><li>Videos</li><li>Lost Certificate</li><li>Immediate Sign Up</li><li>Contact Us</li></ul>

  <h4 class="abs col-title" style="left:492px">MY ACCOUNT</h4>
  <ul class="abs col" style="left:492px"><li>Sign In</li><li>Create an account</li></ul>

  <h4 class="abs col-title" style="left:703px">TERMS &amp; CONDITIONS</h4>
  <ul class="abs col" style="left:703px"><li>Privacy Policy</li><li>Refund Policy</li><li>Terms And Conditions</li><li>Restrictions</li></ul>

  <h4 class="abs col-title" style="left:966px">WE'RE ON SOCIAL</h4>
  <div class="abs social"><span></span><span></span><span></span><span></span></div>

  <div class="abs card"></div>
  <h3 class="abs trainer">DENNIS POLLOCK</h3>
  <p class="abs trainer-role">NFTA FIREARMS INSTRUCTOR, NWDPA INSTRUCTOR &amp; TRAINING COUNSELLOR, NEWS CORRESPONDENT, AND SECURITY EXPERT</p>

  <svg class="abs" style="left:547px;top:2521px" width="14" height="14" viewBox="0 0 14 14"><path d="M3 1l2.5 3-1.5 1.5c.8 1.8 2 3 3.8 3.8L9.3 7.8l3 2.5-1.5 2.5C6 12.5 1.5 8 1.3 3.2Z" fill="#d71f26"/></svg>
  <p class="abs card-info" style="left:577px;top:2520px">LOCAL: 555-014-5SCT (5822)<br>TOLL-FREE: 800-555-0199</p>
  <svg class="abs" style="left:547px;top:2578px" width="14" height="11" viewBox="0 0 14 11"><rect width="14" height="11" fill="#d71f26"/><path d="M0 0l7 6 7-6" fill="none" stroke="#f4f4f4" stroke-width="1.2"/></svg>
  <p class="abs card-info" style="left:577px;top:2575px">steadfieldcarry@example.com</p>
  <svg class="abs" style="left:922px;top:2520px" width="12" height="16" viewBox="0 0 12 16"><path d="M6 0a6 6 0 0 1 6 6c0 4-6 10-6 10S0 10 0 6a6 6 0 0 1 6-6Z" fill="#d71f26"/><circle cx="6" cy="6" r="2.2" fill="#f4f4f4"/></svg>
  <p class="abs card-info" style="left:949px;top:2520px">P.O. Box 4410<br>Cedar Bend,<br>FL 32999</p>

  <p class="abs copy">©2021 Steadfield Carry Training. All Rights Reserved.</p>
</footer>

</body>
</html>
```